Business Card: RW Office Partners - Your organised problem solver

Business Name: RW Office Partners
Website: www.rwofficepartners.com.au
Email: marisol@rwofficepartners.com.au
Mobile: 61 482 907 236
Facebook: @rwofficepartners
Instrgram: @rwofficepartners

Brading Colours:
HEX
#986474
#ddccd3
#7a8498
#c9d8e4
#000000
#ffffff

Tag Line: Your dependable task handler

Link to DRAFT website:
https://deskhelpcollective.wixsite.com/rw-office-partners

About Page from the website:
My name is Marisol Wrenfield, and I would love to assist you to become more productive in your day to day and achieve your business and personal goals.
My mission is to give you time, time to work on the important tasks of your business or to be able to spend more time with your family. I will take on the tasks you don’t have time for, don’t know well or simply don’t like to do.
I have an extensive background in Administration, Tender Coordination, Document Control, WHS and Quality Management working primarily in the Construction, Mining and Corporate World.
I am passionate about being organised, having order and making things in your life (and mine) easier! I love to watch something unfold and grow into something amazing! I am known for being the go-to problem solver, the organiser of all things, producing high standards of work even under pressure. I’m also a confident communicator, and I understand that you’re busy running your business.

Target Market(s)

Small to Medium Business who require assistance in their business by a virtual assistant.

Industry/Entity Type

Virtual Assistant

Contact Information for Business Card

Mobile: 61 482 907 236

Font styles to use
Sans Serif

Colors
ffffff

Requirements
Must have
• Branding Colours as outlined.
Contact Details as outlined.
Logo as provided.
Proper contact details - mobile, facebook, instragm, website.
Simple, Elegant, very clean looking.
Should not have
• Note cute with pictures.
Not too girly as still want to market to construction companies.

```html
<!DOCTYPE html>
<html lang="en">
<head>
<meta charset="utf-8">
<title>RW Office Partners – Business Card</title>
<link href="https://fonts.googleapis.com/css2?family=Roboto:wght@400;500;700&display=swap" rel="stylesheet">
<style>
  :root {
    --backdrop: #3b3b3d;
    --card: #1e1c21;
    --mauve: #986474;
    --slate: #7a8498;
    --white: #ffffff;
  }
  * { margin: 0; padding: 0; box-sizing: border-box; }
  html, body {
    width: 799px; height: 1200px; overflow: hidden;
    background: var(--backdrop);
    font-family: "Roboto", Arial, sans-serif;
  }
  .card {
    position: absolute; left: 70px;
    width: 660px; height: 378px;
    background: var(--card);
    border-radius: 4px;
    overflow: hidden;
    box-shadow: 0 12px 30px rgba(0,0,0,.45);
    color: var(--white);
  }
  .card--front { top: 160px; }
  .card--back { top: 660px; }

  .brand {
    position: absolute;
    display: flex; align-items: center; gap: 16px;
    color: var(--slate);
    font-weight: 500;
    text-transform: uppercase;
    letter-spacing: 1px;
    white-space: nowrap;
  }
  .brand__mark { background: var(--mauve); flex: none; }
  .card--front .brand { left: 0; right: 0; top: 118px; justify-content: center; font-size: 44px; }
  .card--front .brand__mark { width: 34px; height: 34px; }
  .card--back .brand { right: 34px; top: 48px; font-size: 34px; }
  .card--back .brand__mark { width: 26px; height: 26px; }

  .social {
    display: flex; align-items: center; gap: 10px;
    font-size: 18px;
  }
  .social__dot {
    width: 15px; height: 15px; border-radius: 3px;
    background: var(--mauve); flex: none;
  }
  .social-row {
    position: absolute; left: 0; right: 0; top: 250px;
    display: flex; justify-content: center; gap: 30px;
  }

  .person { position: absolute; left: 40px; top: 150px; }
  .person__name { color: var(--mauve); font-weight: 700; font-size: 25px; }
  .person__role { font-size: 16px; margin-top: 4px; }

  .social-list {
    position: absolute; left: 40px; top: 222px;
    display: flex; flex-direction: column; gap: 8px;
  }
  .social-list .social { font-size: 16px; }

  .contact-list {
    position: absolute; left: 355px; top: 200px;
    display: flex; flex-direction: column; gap: 9px;
    list-style: none;
  }
  .contact { display: flex; align-items: center; gap: 12px; font-size: 17px; }
  .contact svg { width: 16px; height: 16px; flex: none; }

  .accent-strip {
    position: absolute; left: 0; top: 300px;
    width: 270px; height: 16px;
    background: var(--slate);
  }
  .tagline-band {
    position: absolute; left: 255px; right: 0; top: 300px; bottom: 0;
    background: var(--mauve);
    border-top-left-radius: 28px;
    display: flex; align-items: center; justify-content: center;
    font-size: 20px;
  }
</style>
</head>
<body>

<section class="card card--front">
  <div class="brand"><span class="brand__mark"></span>RW Office Partners</div>
  <div class="social-row">
    <div class="social"><span class="social__dot"></span>@rwofficepartners</div>
    <div class="social"><span class="social__dot"></span>@rwofficepartners</div>
  </div>
</section>

<section class="card card--back">
  <div class="brand"><span class="brand__mark"></span>RW Office Partners</div>

  <div class="person">
    <p class="person__name">Marisol Wrenfield</p>
    <p class="person__role">Virtual Assistant</p>
  </div>

  <div class="social-list">
    <div class="social"><span class="social__dot"></span>@rwofficepartners</div>
    <div class="social"><span class="social__dot"></span>@rwofficepartners</div>
  </div>

  <ul class="contact-list">
    <li class="contact">
      <svg viewBox="0 0 16 16" aria-hidden="true"><path fill="#986474" d="M3.5 1.5l2.5 0 1 3.5-1.6 1.2a8 8 0 0 0 4.4 4.4L11 9l3.5 1v2.5c0 1-1 2-2 2A11 11 0 0 1 1.5 3.5c0-1 1-2 2-2z"/></svg>
      61 482 907 236
    </li>
    <li class="contact">
      <svg viewBox="0 0 16 16" aria-hidden="true"><rect x="1" y="3" width="14" height="10" rx="1.5" fill="#986474"/><path d="M1.5 4 8 9l6.5-5" fill="none" stroke="#1e1c21" stroke-width="1.4"/></svg>
      marisol@rwofficepartners.com.au
    </li>
    <li class="contact">
      <svg viewBox="0 0 16 16" aria-hidden="true"><g fill="none" stroke="#986474" stroke-width="1.4"><circle cx="8" cy="8" r="6.5"/><ellipse cx="8" cy="8" rx="2.8" ry="6.5"/><path d="M1.5 8h13"/></g></svg>
      www.rwofficepartners.com.au
    </li>
  </ul>

  <div class="accent-strip"></div>
  <div class="tagline-band">Your dependable task handler</div>
</section>

</body>
</html>
```